Bramblewood Joinery Website

My client Bramblewood Joinery is looking for a redesign for a Word Press Website. Their current site is at www.bramblewoodjoinery.example They are a custom cabinet company, but also create bathroom, living room, bar and entertainment and bedroom cabinets too. They would like a design that emulates the master craftsman work they do yet a contemporary style.

Their current site was designed using Flash elements.

Target Market(s)

Home owners and builders of high end homes

Industry/Entity Type

Entertainment

Font styles to use
Serif
Decorative

Requirements
Must have
• Must show their work and logo using a contemporary style.
Nice to have
• Sliders that showcase their projects.

```html
<!DOCTYPE html>
<html lang="en">
<head>
<meta charset="utf-8">
<title>Bramblewood Joinery</title>
<link href="https://fonts.googleapis.com/css2?family=Lato:wght@400;700&family=Montserrat:wght@400;500;600&family=Roboto+Condensed:wght@400;700&family=Kalam&display=swap" rel="stylesheet">
<style>
:root{
  --green:#3cb43c; --green-dark:#2a8a2a; --green-deep:#2e7d2e;
  --ink:#333; --muted:#666; --line:#d8d8d8; --panel:#f3f3f3;
  --footer:#3b3b3b; --footer-bar:#2a2a2a; --footer-text:#bbb;
  --yellow:#f4d21a;
}
*{box-sizing:border-box;margin:0;padding:0}
html,body{width:922px;height:1200px;overflow:hidden;background:#fff}
body{position:relative;font-family:'Montserrat',sans-serif;color:var(--ink)}
.abs{position:absolute}
.header{left:0;top:0;width:922px;height:128px;background:linear-gradient(#3fbb3f,#2f9a34 60%,#2a8b30)}
.brand{left:86px;top:12px;display:flex;align-items:center;gap:8px}
.brand-mark{width:40px;height:40px;border-radius:50%;background:#fff}
.brand-name{color:#fff;font-weight:600;font-size:15px;line-height:1.15;width:120px}
.contacts{right:85px;top:31px;display:flex;gap:14px}
.contact{color:#fff;font-family:'Lato',sans-serif;font-size:12px;display:flex;align-items:center;gap:6px;white-space:nowrap}
.contact .ico{width:22px;height:22px;border:1.5px solid rgba(255,255,255,.6);border-radius:50%;display:flex;align-items:center;justify-content:center}
.nav{left:222px;top:72px;width:615px;height:25px;background:rgba(20,80,20,.35);display:flex;align-items:center;font-size:10.5px;color:#fff;white-space:nowrap}
.nav a{color:#fff;text-decoration:none;padding:0 7.5px;height:25px;line-height:25px}
.nav a.active{background:var(--green)}
.slider{left:84px;top:140px;width:753px;height:334px;border:1px solid #ccc;padding:6px}
.slide-img{width:738px;height:327px;background:linear-gradient(135deg,#ddd6bd 0%,#e8e4d3 35%,#c7b98e 70%,#8a7a5a 100%)}
.caption{left:99px;top:318px;width:370px;height:110px;background:rgba(30,30,30,.82);padding:12px 16px;color:#fff}
.caption h1{font-weight:400;font-size:21px;letter-spacing:.2px;white-space:nowrap;line-height:26px}
.caption h1 b{color:var(--green);font-weight:600}
.caption p{font-family:'Lato',sans-serif;font-size:11px;line-height:15px;margin-top:5px;color:#ddd}
.btn-green{display:inline-block;margin-top:7px;background:var(--green);color:#fff;font-size:9px;padding:4px 10px}
.dots{left:118px;top:448px;display:flex;gap:3px}
.dots i{width:7px;height:7px;border-radius:50%;background:#fff;display:block}
.dots i:first-child{background:var(--green)}
.card{top:491px;width:238px;height:139px;border:2px solid #e6e6e6;overflow:hidden}
.card .photo{position:absolute;right:0;top:0;width:140px;height:135px}
.card .body{position:absolute;left:10px;top:18px;width:140px}
.card h2{color:var(--green);font-size:14.5px;font-weight:600;white-space:nowrap}
.card p{font-family:'Lato',sans-serif;font-size:10px;line-height:14px;color:#555;margin-top:7px}
.more{display:flex;align-items:center;gap:5px;color:var(--green);font-size:10.5px;margin-top:8px}
.more span{width:13px;height:13px;border:1px solid #9c9;border-radius:50%;font-size:10px;line-height:11px;text-align:center}
.guarantee{left:92px;top:645px;width:737px;height:76px;border:1px solid #e0e0e0;background:linear-gradient(90deg,#fff 60%,#eef8ee);overflow:hidden}
.g-title{position:absolute;left:21px;top:9px;display:flex;align-items:center;gap:8px;white-space:nowrap}
.g-title h2{color:var(--green-deep);font-size:21px;font-weight:600}
.g-title .script{font-family:'Kalam',cursive;color:#c0392b;font-size:15px}
.guarantee p{position:absolute;left:21px;top:42px;font-family:'Roboto Condensed',sans-serif;font-size:17px;color:#555;white-space:nowrap}
.guarantee .photo{position:absolute;right:0;top:0;width:198px;height:76px;background:linear-gradient(90deg,rgba(255,255,255,0),#9b6a3c 30%,#6b4526)}
.order{position:absolute;left:529px;top:38px;width:83px;height:26px;border-radius:13px;background:radial-gradient(ellipse at 40% 30%,#ffe95a,var(--yellow) 60%,#c9a40c);color:#222;font-size:10.5px;font-weight:500;text-align:center;line-height:26px;box-shadow:0 2px 3px rgba(0,0,0,.3)}
.panel{top:738px;height:293px;border:1px solid #ddd}
.panel-head{height:28px;background:linear-gradient(#fff,#eee);border-bottom:1px solid #ddd;font-family:'Roboto Condensed',sans-serif;font-weight:700;font-size:13.5px;color:#1e3050;padding:7px 12px}
.products{left:92px;width:183px}
.prod{position:relative;height:41px;padding:4px 0 0 32px;margin:0 5px;border-bottom:1px dashed #ddd}
.prod:before{content:"\203A";position:absolute;left:14px;top:0;font-size:16px;font-weight:700;color:#333}
.prod b{display:block;font-weight:500;color:var(--green);font-size:11.5px}
.prod small{display:block;font-family:'Lato',sans-serif;color:#666;font-size:10px}
.prod.active{background:linear-gradient(#3cb03c,#2a7f2a);margin:0 -1px;padding-left:38px;border:none}
.prod.active:before{color:#fff;left:20px}
.prod.active b,.prod.active small{color:#fff}
.prod.plain{border-bottom:none}
.panel-foot{position:absolute;bottom:0;left:0;right:0;height:16px;background:#eee;border-top:1px solid #ddd;text-align:center;font-size:10px;line-height:14px;color:#555}
.gallery{left:287px;width:543px}
.thumb{position:absolute;width:165px;height:110px;border:1px solid #ccc}
.thumb.active{border:2px solid var(--green)}
.thumb .find{position:absolute;left:0;right:0;bottom:0;height:26px;background:rgba(60,180,60,.6);color:#fff;font-size:10.5px;font-weight:600;text-align:center;line-height:28px}
.footer{left:0;top:1054px;width:922px;height:118px;background:var(--footer);color:#ddd}
.fcol{position:absolute;top:20px}
.fcol h3{font-family:'Lato',sans-serif;font-weight:400;font-size:11px;color:#eee;margin-bottom:8px}
.fcol li{list-style:none;font-family:'Lato',sans-serif;font-size:8.5px;color:var(--footer-text);margin-bottom:6px;padding-left:9px;position:relative;white-space:nowrap}
.fcol li:before{content:"\203A";position:absolute;left:0;top:-1px}
.fcol p{font-family:'Lato',sans-serif;font-size:8px;line-height:11px;color:var(--footer-text)}
.social{display:flex;gap:5px;margin-top:8px}
.social span{width:20px;height:20px;background:#777;border-radius:2px;display:block}
.bottom{left:0;top:1172px;width:922px;height:28px;background:var(--footer-bar);color:#eee;font-size:10.5px;display:flex;align-items:center;justify-content:space-between;padding:0 86px}
</style>
</head>
<body>
<header class="abs header">
  <div class="abs brand"><div class="brand-mark"></div><div class="brand-name">Bramblewood Joinery</div></div>
  <div class="abs contacts">
    <div class="contact"><span class="ico"><svg width="11" height="11" viewBox="0 0 24 24"><path fill="#fff" d="M6.6 10.8a15 15 0 006.6 6.6l2.2-2.2a1 1 0 011-.25 11.4 11.4 0 003.6.6 1 1 0 011 1V20a1 1 0 01-1 1A17 17 0 013 4a1 1 0 011-1h3.5a1 1 0 011 1c0 1.25.2 2.45.6 3.6a1 1 0 01-.25 1z"/></svg></span>123 456 789</div>
    <div class="contact"><span class="ico"><svg width="11" height="9" viewBox="0 0 22 16"><rect x="1" y="1" width="20" height="14" fill="none" stroke="#fff" stroke-width="2"/><path d="M1 1l10 8 10-8" fill="none" stroke="#fff" stroke-width="2"/></svg></span>info@bramblewoodjoinery.example</div>
  </div>
  <nav class="abs nav">
    <a class="active" href="#">Home</a><a href="#">Who We Are</a><a href="#">Getting Started</a><a href="#">Contact Us</a><a href="#">Customer Experience</a><a href="#">Professional</a><a href="#">Cabinet Hardware</a>
  </nav>
</header>

<section class="abs slider">
  <div class="slide-img" role="img" aria-label="Bright white kitchen with glass-front cabinets, granite worktops and a steel range hood"></div>
</section>
<div class="abs caption">
  <h1>WELCOME TO <b>BRAMBLEWOOD</b></h1>
  <p>Lorem ipsum dolor sit amet consectetur adipiscing tempor<br>incididunt ut labore magna aliqua.</p>
  <span class="btn-green">Learn More</span>
</div>
<div class="abs dots"><i></i><i></i><i></i><i></i></div>

<article class="abs card" style="left:92px">
  <div class="photo" role="img" aria-label="Kitchen with warm orange wood cabinets" style="background:linear-gradient(90deg,#fff,#e6a060 45%,#b8642a)"></div>
  <div class="body"><h2>Cabinets &amp; Drawer</h2><p>Lorem ipsum dolor sit amet, consectetur adipi-scing elit, sed.</p><div class="more"><span>+</span>Learn More</div></div>
</article>
<article class="abs card" style="left:342px">
  <div class="photo" role="img" aria-label="Kitchen with white cabinets and dark island" style="background:linear-gradient(90deg,#fff,#c9c6c0 45%,#6d6458)"></div>
  <div class="body"><h2>Cabinets &amp; Drawer</h2><p>Lorem ipsum dolor sit amet, consectetur adipi-scing elit, sed.</p><div class="more"><span>+</span>Learn More</div></div>
</article>
<article class="abs card" style="left:591px">
  <div class="photo" role="img" aria-label="Kitchen with white cabinetry and dark floor" style="background:linear-gradient(90deg,#fff,#e4e4e2 45%,#8a8782)"></div>
  <div class="body"><h2>Cabinets &amp; Drawer</h2><p>Lorem ipsum dolor sit amet, consectetur adipi-scing elit, sed.</p><div class="more"><span>+</span>Learn More</div></div>
</article>

<section class="abs guarantee">
  <div class="photo" role="img" aria-label="Kitchen with dark wood cabinets and steel fridge"></div>
  <div class="g-title">
    <h2>Perfect Fit Guarantee</h2>
    <svg width="30" height="12" viewBox="0 0 30 12"><path d="M1 7c8-2 18-1 27-1M22 2l6 4-6 4" fill="none" stroke="#3cb43c" stroke-width="1.5"/></svg>
    <span class="script">for a free!</span>
  </div>
  <p>For a fee we will come measure the kitchen and guarantee a perfect fit.</p>
  <span class="order">Order Now</span>
</section>

<aside class="abs panel products">
  <div class="panel-head">Products</div>
  <div class="prod"><b>Office</b><small>Lorem Ipsum</small></div>
  <div class="prod active"><b>Kitchen</b><small>Lorem Ipsum</small></div>
  <div class="prod"><b>Bath</b><small>Lorem Ipsum</small></div>
  <div class="prod"><b>Dressing</b><small>Lorem Ipsum</small></div>
  <div class="prod"><b>Workshop</b><small>Lorem Ipsum</small></div>
  <div class="prod plain"><b>Entertainment</b><small>Lorem Ipsum</small></div>
  <div class="panel-foot">&#8964;</div>
</aside>

<section class="abs panel gallery">
  <div class="panel-head">Picture Gallery</div>
  <div class="thumb active" style="left:11px;top:42px;background:linear-gradient(#d9d4c8,#a9a294)" role="img" aria-label="Kitchen with steel range cooker"><div class="find">Find Out More</div></div>
  <div class="thumb" style="left:189px;top:42px;background:linear-gradient(135deg,#c7a46a,#7a4f28)" role="img" aria-label="Open kitchen with wood cabinets and bar"></div>
  <div class="thumb" style="left:365px;top:42px;background:linear-gradient(135deg,#e8e6e0,#b54040 50%,#c9b58c)" role="img" aria-label="Kitchen corner with red blind"></div>
  <div class="thumb" style="left:11px;top:167px;background:linear-gradient(135deg,#e8e6e0,#b54040 50%,#c9a070)" role="img" aria-label="Kitchen with window and red blind"></div>
  <div class="thumb" style="left:189px;top:167px;background:linear-gradient(135deg,#4a3f32,#8f7a56 50%,#3a3128)" role="img" aria-label="Rustic kitchen with wood stove"></div>
  <div class="thumb" style="left:365px;top:167px;background:linear-gradient(135deg,#f2f0ea,#d9ccaa)" role="img" aria-label="White kitchen with cooker and fridge"></div>
</section>

<footer class="abs footer">
  <div class="fcol" style="left:86px"><h3>Quicklink</h3><ul><li>Site Map</li><li>About Us</li><li>Privacy Policy</li></ul></div>
  <div class="fcol" style="left:174px"><h3>Navigation</h3><ul><li>Home</li><li>Who We Are</li><li>Getting started Consectetur</li><li>Contact Us Lorem Ipsum</li></ul></div>
  <div class="fcol" style="left:323px"><h3>Lorem Ipsum</h3><ul><li>Amet</li><li>Sit</li><li>Consectetur</li><li>Lorem Ipsum</li></ul></div>
  <div class="fcol" style="left:465px;width:140px"><h3>Contact Us</h3><p>Lorem Ipsum is simply dummy text of the printing and typesetting.</p><p style="font-size:10px;margin-top:5px;color:#888">&#9742; 123 654 789</p></div>
  <div class="fcol" style="left:630px"><h3>Social Media</h3><p style="font-size:10px;color:#888;margin-top:14px">Connect With Us</p><div class="social"><span></span><span></span><span></span><span></span><span></span></div></div>
</footer>
<div class="abs bottom"><span>© 2015 bramblewoodjoinery.example All Right Reserved.</span><span>Terms &nbsp;|&nbsp; Privacy Policy</span></div>
</body>
</html>
```